Landscaping flier 2024

Create a 1 page flier for landscaping services
1. Must be completed in Adobe Photoshop
2. Size 8.5" x 11" (portrait layout)
3. Include logo
4. Text to include:
2024 Gravesite Landscaping Packages
info@hollowbrookmemorial.org
(201) 555-0148
hollowbrookmemorial.org
5. Use chart text for the content. DO NOT COPY THE CHART DESIGN/FORMAT. Use the chart for the text you need only.
6. Use "Pricing cards as format for laying out the chart". Open to other ideas as well.
**Use the example of chart design (handwritten) to base your design off of.
7. Photos
-include before and after care photos

```html
<!DOCTYPE html>
<html lang="en">
<head>
<meta charset="utf-8">
<title>2024 Gravesite Landscaping Packages</title>
<link href="https://fonts.googleapis.com/css2?family=Poppins:wght@400;500;700;800&family=Great+Vibes&display=swap" rel="stylesheet">
<style>
:root{
  --page:#e4e4e4;
  --paper:#ffffff;
  --maroon:#7a1d2a;
  --rose:#b23247;
  --seasonal:#b53a50;
  --basic:#c52338;
  --perpetual:#8e2236;
  --band:#6e1a1e;
  --footer:#7c1a2b;
  --footer-light:#b02a43;
  --panel:#ffffff;
  --panel-head:#eef0f1;
  --rule:#d4d6d8;
  --ink:#2a2a2a;
  --light:#ffffff;
}
*{margin:0;padding:0;box-sizing:border-box}
html,body{width:1200px;height:2824px;overflow:hidden;background:var(--page);font-family:'Poppins',sans-serif;color:var(--ink)}
.flyer{position:absolute;left:30px;top:672px;width:1140px;height:1480px;background:linear-gradient(135deg,#fafafa 0%,#eef0f1 45%,#fbfbfb 100%);overflow:hidden;box-shadow:0 6px 24px rgba(0,0,0,.18)}
.abs{position:absolute}
.brand{left:70px;top:40px;width:260px;text-align:center}
.brand-mark{width:150px;height:150px;border-radius:50%;background:#d9dadb;margin:0 auto 14px}
.brand-name{font-weight:700;color:var(--maroon);font-size:40px;line-height:1.1;letter-spacing:1px}
.title{left:420px;top:42px;width:490px;text-align:center;font-weight:800;line-height:1.17}
.title .year{color:var(--maroon);font-size:58px;display:block}
.title .big{color:var(--rose);font-size:58px;display:block;letter-spacing:1px}
.band{left:23px;top:542px;width:1080px;height:412px;background:var(--band);border-radius:18px 0 0 18px}
.services-title{left:53px;top:462px;font-weight:800;font-size:29px;line-height:1.18;color:var(--maroon)}
.service{left:41px;width:195px;color:var(--light);font-size:18px;line-height:1.2}
.service-rule{left:41px;width:195px;height:1px;background:rgba(255,255,255,.55)}
.card{top:322px;width:251px;height:786px;border-radius:16px;color:var(--light);text-align:center}
.card.seasonal{left:263px;background:var(--seasonal)}
.card.basic{left:555px;background:var(--basic)}
.card.perpetual{left:849px;background:var(--perpetual)}
.card-name{position:absolute;left:0;right:0;top:30px;font-weight:800;font-size:29px;line-height:1.2}
.card.perpetual .card-name{top:14px;font-size:27px;letter-spacing:-.3px;padding-right:14px}
.panel{top:449px;width:225px;height:500px;background:var(--panel);border-radius:0 0 12px 12px;text-align:center;box-shadow:0 3px 8px rgba(0,0,0,.15)}
.panel-head{height:96px;background:var(--panel-head);font-size:20px;line-height:1.2;padding:14px 6px 0;color:var(--ink)}
.panel-detail{height:92px;font-size:13.5px;line-height:1.15;padding:10px 2px 0;border-bottom:1px solid var(--rule);margin:0 8px;overflow:hidden}
.mark{position:absolute;left:0;right:0;height:40px;display:flex;align-items:center;justify-content:center;font-weight:700;font-size:26px;color:var(--maroon)}
.mark svg{width:34px;height:30px}
.row-rule{position:absolute;left:10px;right:10px;height:1px;background:var(--rule)}
.price{left:0;width:100%;text-align:center;font-size:18px;line-height:1.15}
.price strong{font-weight:700}
.big-price{font-weight:700;font-size:35px}
.popular{left:1048px;top:268px;width:86px;height:86px;border-radius:50%;background:var(--light);border:2px solid var(--basic);font-family:'Great Vibes',cursive;color:var(--maroon);font-size:23px;line-height:.95;text-align:center;padding-top:17px;transform:rotate(-8deg)}
.valid{left:57px;top:980px;font-size:14px;color:var(--maroon)}
.footer-wave{left:0;top:1100px;width:1140px;height:380px}
.photo{background:var(--light);padding:12px;box-shadow:0 4px 12px rgba(0,0,0,.3)}
.photo .shot{width:100%;height:100%;background:linear-gradient(180deg,#8f9a8c 0%,#6f9a4e 35%,#4f8f34 100%)}
.photo.before{left:538px;top:1118px;width:270px;height:262px;transform:rotate(-5deg)}
.photo.after{left:812px;top:1112px;width:248px;height:250px;transform:rotate(3deg)}
.photo-label{color:var(--light);font-size:28px}
.contact{left:52px;color:var(--light);font-weight:700;display:flex;align-items:center;gap:16px}
.contact svg{width:28px;height:28px;fill:var(--light)}
</style>
</head>
<body>
<div class="flyer">

  <div class="abs brand">
    <div class="brand-mark"></div>
    <div class="brand-name">HOLLOWBROOK<br>MEMORIAL</div>
  </div>

  <h1 class="abs title"><span class="year">2024 Gravesite</span><span class="big">LANDSCAPING</span><span class="big">PACKAGES</span></h1>

  <div class="abs band"></div>

  <div class="abs services-title">SERVICES<br>OFFERED</div>
  <div class="abs service" style="top:579px">Weeding &amp; trimming on your gravesite</div>
  <div class="abs service" style="top:652px">Payment ensures grave care forever</div>
  <div class="abs service-rule" style="top:702px"></div>
  <div class="abs service" style="top:710px">Monument leveling</div>
  <div class="abs service-rule" style="top:749px"></div>
  <div class="abs service" style="top:758px">Monument cleaning</div>
  <div class="abs service-rule" style="top:796px"></div>
  <div class="abs service" style="top:806px">Full bed of<br>Boxwood shrubs</div>
  <div class="abs service-rule" style="top:866px"></div>
  <div class="abs service" style="top:877px">Trust certificate</div>

  <div class="abs card seasonal">
    <div class="card-name">SEASONAL<br>CARE</div>
    <div class="abs price" style="top:642px">3 Year&nbsp;&nbsp;<strong>$396</strong></div>
    <div class="abs price" style="top:675px">2Year&nbsp;&nbsp;<strong>$264</strong></div>
    <div class="abs price" style="top:708px">1Year&nbsp;&nbsp;<strong>$132</strong></div>
    <div class="abs price" style="top:738px;font-size:17px">Multi-year payment<br>local in current rates.</div>
  </div>
  <div class="abs panel" style="left:249px">
    <div class="panel-head">Seasonal landscaping grave care.</div>
    <div class="panel-detail">Approximately every 7 weeks during the growing season: mid-April through mid-October</div>
    <div class="mark" style="top:197px">X</div>
    <div class="row-rule" style="top:253px"></div>
    <div class="mark" style="top:255px">X</div>
    <div class="row-rule" style="top:300px"></div>
    <div class="mark" style="top:303px">X</div>
    <div class="row-rule" style="top:347px"></div>
    <div class="mark" style="top:364px">X</div>
    <div class="row-rule" style="top:417px"></div>
    <div class="mark" style="top:422px">X</div>
  </div>

  <div class="abs card basic">
    <div class="card-name">BASIC CARE<br>ENDOWMENT</div>
    <div class="abs price" style="top:648px">12 month payment</div>
    <div class="abs price big-price" style="top:676px">$287</div>
    <div class="abs price" style="top:738px;font-size:17px">Call for single payment<br>discount</div>
  </div>
  <div class="abs panel" style="left:543px">
    <div class="panel-head">Landscaping care forever for graves with no plantings</div>
    <div class="panel-detail">2 times year:<br>mid-May &amp; mid-<br>September</div>
    <div class="mark" style="top:197px"><svg viewBox="0 0 34 30"><path d="M3 16 L12 26 L31 3" fill="none" stroke="currentColor" stroke-width="5" stroke-linecap="round" stroke-linejoin="round"/></svg></div>
    <div class="row-rule" style="top:253px"></div>
    <div class="mark" style="top:255px"><svg viewBox="0 0 34 30"><path d="M3 16 L12 26 L31 3" fill="none" stroke="currentColor" stroke-width="5" stroke-linecap="round" stroke-linejoin="round"/></svg></div>
    <div class="row-rule" style="top:300px"></div>
    <div class="mark" style="top:303px">X</div>
    <div class="row-rule" style="top:347px"></div>
    <div class="mark" style="top:364px">X</div>
    <div class="row-rule" style="top:417px"></div>
    <div class="mark" style="top:422px">X</div>
  </div>

  <div class="abs card perpetual">
    <div class="card-name">PERPETUAL<br>CARE EN<br>DOWMENT</div>
    <div class="abs price" style="top:648px">12 month payment</div>
    <div class="abs price big-price" style="top:676px">$351</div>
    <div class="abs price" style="top:738px;font-size:17px">Call for single payment<br>discount</div>
  </div>
  <div class="abs panel" style="left:837px">
    <div class="panel-head">Landscaping care forever for graves with no plantings</div>
    <div class="panel-detail">Approxi mately every 7 weeks during the growing season: mid-April through mid-October</div>
    <div class="mark" style="top:197px"><svg viewBox="0 0 34 30"><path d="M3 16 L12 26 L31 3" fill="none" stroke="currentColor" stroke-width="5" stroke-linecap="round" stroke-linejoin="round"/></svg></div>
    <div class="row-rule" style="top:253px"></div>
    <div class="mark" style="top:255px"><svg viewBox="0 0 34 30"><path d="M3 16 L12 26 L31 3" fill="none" stroke="currentColor" stroke-width="5" stroke-linecap="round" stroke-linejoin="round"/></svg></div>
    <div class="row-rule" style="top:300px"></div>
    <div class="mark" style="top:303px"><svg viewBox="0 0 34 30"><path d="M3 16 L12 26 L31 3" fill="none" stroke="currentColor" stroke-width="5" stroke-linecap="round" stroke-linejoin="round"/></svg></div>
    <div class="row-rule" style="top:347px"></div>
    <div class="mark" style="top:364px"><svg viewBox="0 0 34 30"><path d="M3 16 L12 26 L31 3" fill="none" stroke="currentColor" stroke-width="5" stroke-linecap="round" stroke-linejoin="round"/></svg></div>
    <div class="row-rule" style="top:417px"></div>
    <div class="mark" style="top:422px"><svg viewBox="0 0 34 30"><path d="M3 16 L12 26 L31 3" fill="none" stroke="currentColor" stroke-width="5" stroke-linecap="round" stroke-linejoin="round"/></svg></div>
  </div>

  <div class="abs popular">Most<br>Popular</div>

  <div class="abs valid">Valid through 10/31/2024</div>

  <svg class="abs footer-wave" viewBox="0 0 1140 380" preserveAspectRatio="none">
    <path d="M0 95 C160 40 300 110 440 170 C600 240 800 230 1140 215 L1140 380 L0 380 Z" fill="var(--footer)"/>
    <path d="M560 380 C760 300 960 220 1140 170 L1140 380 Z" fill="var(--footer-light)"/>
  </svg>

  <div class="abs photo before"><div class="shot" role="img" aria-label="Before photo: overgrown grave plot in front of a headstone"></div></div>
  <div class="abs photo after"><div class="shot" role="img" aria-label="After photo: trimmed shrubs and tidy lawn in front of the headstone"></div></div>
  <div class="abs photo-label" style="left:645px;top:1413px;transform:rotate(-6deg)">Before</div>
  <div class="abs photo-label" style="left:905px;top:1394px">After</div>

  <div class="abs contact" style="top:1330px;font-size:35px">
    <svg viewBox="0 0 24 24"><path d="M6.6 10.8a15.1 15.1 0 0 0 6.6 6.6l2.2-2.2c.3-.3.7-.4 1-.2 1.1.4 2.3.6 3.6.6.6 0 1 .4 1 1V20c0 .6-.4 1-1 1C10.6 21 3 13.4 3 4c0-.6.4-1 1-1h3.5c.6 0 1 .4 1 1 0 1.3.2 2.5.6 3.6.1.3 0 .7-.2 1z"/></svg>
    (201) 555-0148</div>
  <div class="abs contact" style="top:1389px;font-size:27px">
    <svg viewBox="0 0 24 24"><path d="M2 5h20v14H2zM3.5 6.5 12 13l8.5-6.5v-.1H3.5zm0 2V17.5h17V8.5L12 15z"/></svg>
    info@hollowbrookmemorial.org</div>
  <div class="abs contact" style="top:1433px;font-size:27px">
    <svg viewBox="0 0 24 24"><path d="M12 2a10 10 0 1 0 0 20 10 10 0 0 0 0-20zm6.9 6h-2.9a15 15 0 0 0-1.3-3.6A8 8 0 0 1 18.9 8zM12 4c.8 1.2 1.5 2.5 1.9 4h-3.8c.4-1.5 1.1-2.8 1.9-4zM4.3 14a8 8 0 0 1 0-4h3.4a16 16 0 0 0 0 4zm.8 2h2.9c.3 1.3.8 2.5 1.3 3.6A8 8 0 0 1 5.1 16zM8 8H5.1a8 8 0 0 1 4.2-3.6C8.8 5.5 8.3 6.7 8 8zm4 12c-.8-1.2-1.5-2.5-1.9-4h3.8c-.4 1.5-1.1 2.8-1.9 4zm2.3-6H9.7a14 14 0 0 1 0-4h4.6a14 14 0 0 1 0 4zm.4 5.6c.5-1.1 1-2.3 1.3-3.6h2.9a8 8 0 0 1-4.2 3.6zm1.6-5.6a16 16 0 0 0 0-4h3.4a8 8 0 0 1 0 4z"/></svg>
    hollowbrookmemorial.org</div>

</div>
</body>
</html>
```